Website redesign for job agency recruitment

Please refer to the attached document, “Tarvenly Work Website Brief,” for comprehensive details regarding the scope, objectives, and requirements of this website redesign project.

For imagery you can use images from this website https://www.pixelmarrowfoto.com or any other you regularly use.

Target Market(s)

Jobseekers and Companies looking for general labour

Industry/Entity Type

Services: Oil, Gas and Mining, Administrative, Construction and Trades, Warehouse and Logistics and, Manufacturing.

Number of Pages Required

5+ page

Font styles to use
Serif
Other font styles liked:
• Inter, Open-Sans or similar.

Requirements
Must have
• The requirements highlighted in the Word document attached. The final design needs to be provided in Figma including all viewports (Desktop, mobiel and tablet)
Should not have
• Website we like as a reference: www.brevicktalentco.com, www.qelvaworks.com, www.zunmarra.com, www.ferrowhires.com, www.9vtalentpool.com, www.hiringwithtrello.ca

```html
<!DOCTYPE html>
<html lang="en">
<head>
<meta charset="utf-8">
<title>Tarvenly Work Agency</title>
<link href="https://fonts.googleapis.com/css2?family=Poppins:wght@400;500;600&display=swap" rel="stylesheet">
<style>
:root{
  --gold:#b8962a;
  --navy:#1b2c57;
  --ink:#1e2b4f;
  --cream:#f7f4ec;
  --white:#ffffff;
  --muted:#444c5e;
}
*{margin:0;padding:0;box-sizing:border-box}
html,body{width:1200px;height:2327px;overflow:hidden;background:var(--white);font-family:'Poppins',sans-serif;color:var(--ink)}
.page{position:relative;width:1200px;height:2327px}
.abs{position:absolute}

.header{left:0;top:0;width:1200px;height:82px;background:#f6f6f8;border-bottom:1px solid #e4e4ea}
.brand{left:60px;top:16px;display:flex;align-items:center;gap:8px}
.brand-mark{width:30px;height:30px;border-radius:50%;background:var(--gold)}
.brand-name{font-size:16px;font-weight:600;color:var(--navy);line-height:1.1}
.brand-tag{font-size:7px;color:#777;display:block;font-weight:400}
.nav a{position:absolute;top:30px;font-size:15px;color:#555a66;text-decoration:none}
.nav a.current{color:var(--navy);font-weight:600;text-decoration:underline;text-underline-offset:4px}

.hero{left:0;top:82px;width:1200px;height:603px;background:linear-gradient(100deg,#2a2f4a 0%,#5b4a72 35%,#b0607e 60%,#d4849a 75%,#3a2f4a 100%)}
.hero-title{left:49px;top:170px;font-size:54px;font-weight:500;line-height:66px;color:var(--white)}
.btn{position:absolute;background:var(--gold);color:var(--white);font-weight:500;display:flex;align-items:center;justify-content:center;border-radius:8px;letter-spacing:2px}
.hero-btn{top:428px;width:193px;height:59px;font-size:20px;border-radius:10px}

.banner{left:60px;top:697px;width:1080px;height:68px;background:var(--navy);border-radius:12px}
.banner-text{left:30px;top:19px;font-size:22px;color:var(--white)}
.apply{left:857px;top:15px;width:193px;height:36px;font-size:19px;border-radius:6px}

.services{left:0;top:776px;width:1200px;height:1115px;background:var(--cream)}
.services h2{position:absolute;left:60px;top:96px;font-size:40px;font-weight:600;color:var(--navy)}
.services p{position:absolute;left:65px;top:182px;width:320px;font-size:19px;line-height:28.5px;color:var(--muted)}
.card{position:absolute;border-radius:10px;overflow:hidden}
.card .shade{position:absolute;inset:0;background:linear-gradient(180deg,rgba(10,15,30,.05) 40%,rgba(10,15,30,.55) 100%)}
.card-label{position:absolute;left:27px;bottom:82px;font-size:23px;font-weight:500;color:var(--white)}
.read-more{position:absolute;left:27px;bottom:27px;height:40px;width:142px;background:var(--gold);border-radius:5px;color:var(--white);font-size:16px;font-weight:600;display:flex;align-items:center;justify-content:center;gap:8px}

.project{left:0;top:1891px;width:1200px;text-align:center}
.project h2{margin-top:46px;font-size:40px;font-weight:500;color:var(--navy)}
.project p{margin:34px auto 0;width:680px;font-size:14px;line-height:24px;color:#3b4256}
.project p u{color:var(--navy)}
.call{left:503px;top:2117px;width:206px;height:50px;font-size:17px;border-radius:10px}
.copyright{left:0;top:2199px;width:1200px;text-align:center;font-size:12px;color:#3b4256}
.copyright u{color:var(--gold)}
.rule{left:60px;top:2249px;width:1080px;height:1px;background:#9aa0ad}
.footer-nav a{position:absolute;top:2274px;font-size:12px;letter-spacing:1.2px;color:var(--ink);text-decoration:none;font-weight:500}
.social{top:2268px;width:31px;height:31px;border:1.5px solid var(--ink);border-radius:5px}
</style>
</head>
<body>
<div class="page">

  <header class="header abs">
    <div class="brand abs">
      <span class="brand-mark"></span>
      <span class="brand-name">Tarvenly<span class="brand-tag">Right people, right roles</span></span>
    </div>
    <nav class="nav">
      <a class="current" style="left:353px">Home</a>
      <a style="left:448px">Candidates</a>
      <a style="left:586px">Companies</a>
      <a style="left:723px">About Us</a>
      <a style="left:839px">Contacts</a>
      <a style="left:958px">Forms &amp; Links</a>
    </nav>
    <svg class="abs" style="left:1117px;top:29px" width="24" height="24" viewBox="0 0 24 24" fill="none" stroke="#555a66" stroke-width="2"><circle cx="10" cy="10" r="7"/><line x1="15" y1="15" x2="21" y2="21"/></svg>
  </header>

  <section class="hero abs" role="img" aria-label="Two business people at a high-rise window overlooking a city skyline at a pink sunset">
    <h1 class="hero-title abs">Our Goal Is<br>Your<br>Success</h1>
    <span class="btn hero-btn" style="left:49px">Companies</span>
    <span class="btn hero-btn" style="left:254px">Candidates</span>
  </section>

  <div class="banner abs">
    <span class="banner-text abs">Tarvenly Work Agency offer various opportunities in the different industries.</span>
    <span class="btn apply">Apply Here</span>
  </div>

  <section class="services abs">
    <h2>Our Services</h2>
    <p>Whether you’re searching for work or hiring staff, we simplify the process with reliable job listings and recruitment support</p>

    <div class="card" style="left:434px;top:52px;width:706px;height:335px;background:linear-gradient(120deg,#2b3440,#4a5560 50%,#24405c)" role="img" aria-label="Factory workers in hard hats operating machinery on a manufacturing floor">
      <div class="shade"></div>
      <span class="card-label">Manufacturing</span>
      <span class="read-more">Read More <svg width="20" height="10" viewBox="0 0 20 10" fill="none" stroke="#fff" stroke-width="1.8"><line x1="1" y1="5" x2="18" y2="5"/><polyline points="13,1 18,5 13,9"/></svg></span>
    </div>

    <div class="card" style="left:60px;top:404px;width:357px;height:311px;background:linear-gradient(130deg,#1f2b44,#2d4a70 60%,#1a2236)" role="img" aria-label="Office professionals in business suits holding folders">
      <div class="shade"></div>
      <span class="card-label">Administrative</span>
      <span class="read-more">Read More <svg width="20" height="10" viewBox="0 0 20 10" fill="none" stroke="#fff" stroke-width="1.8"><line x1="1" y1="5" x2="18" y2="5"/><polyline points="13,1 18,5 13,9"/></svg></span>
    </div>

    <div class="card" style="left:434px;top:404px;width:344px;height:311px;background:linear-gradient(160deg,#3d5f9a,#6f7f94 50%,#8a6a3c)" role="img" aria-label="Construction site with tower cranes and workers in safety vests">
      <div class="shade"></div>
      <span class="card-label">Construction</span>
      <span class="read-more">Read More <svg width="20" height="10" viewBox="0 0 20 10" fill="none" stroke="#fff" stroke-width="1.8"><line x1="1" y1="5" x2="18" y2="5"/><polyline points="13,1 18,5 13,9"/></svg></span>
    </div>

    <div class="card" style="left:795px;top:404px;width:345px;height:311px;background:linear-gradient(180deg,#1c2a3c,#2f4a5e 50%,#3a3a44)" role="img" aria-label="Large warehouse aisle lined with tall storage racks">
      <div class="shade"></div>
      <span class="card-label">WareHouse &amp; Logistics</span>
      <span class="read-more">Read More <svg width="20" height="10" viewBox="0 0 20 10" fill="none" stroke="#fff" stroke-width="1.8"><line x1="1" y1="5" x2="18" y2="5"/><polyline points="13,1 18,5 13,9"/></svg></span>
    </div>

    <div class="card" style="left:60px;top:731px;width:1080px;height:332px;background:linear-gradient(100deg,#5a3a2c,#4a4a50 35%,#5d6068 65%,#3f4a58)" role="img" aria-label="Worker in hard hat and orange coveralls looking at an offshore oil platform">
      <div class="shade"></div>
      <span class="card-label">Oil,Gas &amp; Mining</span>
      <span class="read-more">Read More <svg width="20" height="10" viewBox="0 0 20 10" fill="none" stroke="#fff" stroke-width="1.8"><line x1="1" y1="5" x2="18" y2="5"/><polyline points="13,1 18,5 13,9"/></svg></span>
    </div>
  </section>

  <section class="project abs">
    <h2>Let's delve into the specifics of your project!</h2>
    <p>We value your <u>privacy</u> and are committed to protecting your personal information. We do not sell, trade, or share your personal data with third-party entities for marketing or promotional purposes.</p>
  </section>
  <span class="btn call">Schedule a Call</span>
  <div class="copyright abs">© Tarvenly Work Agency Ltd. | All rights reserved 2024 | <u>Terms of Use</u> | <u>Login</u></div>

  <div class="rule abs"></div>
  <nav class="footer-nav">
    <a style="left:323px">HOME</a>
    <a style="left:393px">Candidate</a>
    <a style="left:497px">Company</a>
    <a style="left:595px">About us</a>
    <a style="left:688px">CONTACT</a>
    <a style="left:784px">Form &amp; Links</a>
  </nav>
  <span class="social abs" style="left:1020px"></span>
  <span class="social abs" style="left:1064px"></span>
  <span class="social abs" style="left:1108px"></span>

</div>
</body>
</html>
```